Kelumo.cn needs pages to be re-designed

www.kelumo.cn is our current new site which was launched in April.
We're a financial services website in the crowdfunding space in China to connect borrower's and lender's.

test.kelumo.cn is our test site
u: test
p: newtest
http://test.kelumo.cn/
http://test.kelumo.cn/user/accounts/new_lender
http://test.kelumo.cn/user/accounts/new_borrower
http://test.kelumo.cn/introductions/protection
http://test.kelumo.cn/introductions
http://test.kelumo.cn/introductions/kelumo_admin
http://test.kelumo.cn/introductions/contact
Some of the pages have pop-ups in the bloc's of the pages. Please click the links, to see more content.

User's currently criticize the website for being:
- Too Western looking
- Too simple, too little content
- Content NOT in the pop-ups are too simple
- Pictures are too big and too much blank space
- Relevant information is not there when needed
- The pictures are too generic

What we would like to do is re-design those pages with the same color scheme and style to be more compelling, efficient, non-intimidating and easy-to-use. Our audience is Ages 25-35 predominantly male investors.
We are looking for more ideas to make the content match the style, while bridging western and chinese design. Our ultimate goal is to increase registrants to the website and highlight our core competitive advantages.

Some competitors websites are:
www.fobuxiqi.com
www.tamev.com
www.zzzlendo.com

Reason: Not enough good designs that follow the prompt. Same style, better information layout!

Reason: Still have not received a design we're satisfied with

Reason: WE DONT WANT A COMPLETE REDESIGN OF PAGES . KEEP THE EXACT SAME COLOR AND STYLE - WE WANT CONTENT RE-DESIGN! THE BLOCS ARE TOO SIMPLE - WE WANT MORE CONTENT INSIDE.

Reason: no new designs

Reason: no new designs

Reason: other non-registered pages need to be re-designed

```html
<!DOCTYPE html>
<html lang="zh-CN">
<head>
<meta charset="utf-8">
<title>Kelumo.cn</title>
<link rel="stylesheet" href="https://fonts.googleapis.com/css2?family=Noto+Sans+SC:wght@400;500;700&display=swap">
<style>
:root{
  --green:#4cb62a;
  --green-dark:#3a9a1e;
  --green-text:#5cae2b;
  --blue:#2aa6e0;
  --ink:#333;
  --muted:#777;
  --line:#e3e3e3;
  --topbar:#4a4d52;
  --footer:#2b2e34;
  --band:#ececec;
  --orange:#f6a23d;
  --yellow:#f2c81c;
  --pink:#ec6676;
  --purple:#9a7096;
}
*{box-sizing:border-box;margin:0;padding:0}
html,body{width:1200px;height:2457px;overflow:hidden}
body{position:relative;background:#fff;font-family:"Noto Sans SC",sans-serif;color:var(--ink)}
.abs{position:absolute}
/* top bar */
.topbar{position:absolute;left:0;top:0;width:1200px;height:37px;background:var(--topbar)}
.topbar > *{position:absolute}
.topbar .field{top:8px;height:22px;width:200px;background:#fff;border-radius:2px;font-size:11px;line-height:22px;color:#999;padding:0 8px;white-space:nowrap;overflow:hidden}
.topbar .login{left:774px;top:8px;width:86px;height:22px;background:var(--green);color:#fff;font-size:12px;text-align:center;line-height:22px;border-radius:2px}
.topbar .hint{left:876px;top:8px;line-height:22px;color:#fff;font-size:12px;white-space:nowrap}
.topbar .lang{left:1005px;top:8px;width:40px;height:22px;background:#e9e9e9;border-radius:2px;display:flex;align-items:center;justify-content:center;gap:5px}
.topbar .lang i{width:14px;height:10px;background:#c33}
.topbar .lang b{width:0;height:0;border-left:4px solid transparent;border-right:4px solid transparent;border-top:5px solid #555}
/* header */
.header{left:0;top:37px;width:1200px;height:86px;background:linear-gradient(#fafafa,#ececec)}
.brand{left:139px;top:57px;display:flex;align-items:center;gap:10px}
.brand .dot{width:44px;height:44px;border-radius:50%;background:var(--green)}
.brand .name{font-size:26px;font-weight:700;color:var(--green-text)}
.nav a{position:absolute;top:70px;font-size:18px;color:#333;text-decoration:none;transform:translateX(-50%);white-space:nowrap}
/* hero */
.hero{left:0;top:123px;width:1200px;height:327px;background:linear-gradient(90deg,#bfb8b2 0%,#d9d9d9 40%,#9ea4aa 70%,#c9cdd1 100%)}
.hero-title{left:655px;top:190px;font-size:40px;line-height:56px;font-weight:500;color:#222}
.hero-text{left:700px;top:300px;font-size:16px;line-height:25px;color:#333}
/* strip */
.strip{left:0;top:450px;width:1200px;height:128px;background:#f3f4f4;border-bottom:1px solid var(--line)}
.strip-slogan{left:139px;top:482px;font-size:22px;line-height:38px;color:var(--green-text)}
.strip-mid{left:505px;top:488px;font-size:22px;color:#333}
.strip-date{left:768px;top:526px;font-size:13px;color:#666}
.btn{background:var(--green);color:#fff;border-radius:20px;text-align:center;font-weight:500;box-shadow:0 2px 0 var(--green-dark)}
.strip-btn{left:932px;top:494px;width:125px;height:42px;line-height:42px;font-size:17px}
/* features */
.feature{top:610px;width:300px;text-align:center;transform:translateX(-50%)}
.feature .icon{width:62px;height:62px;border-radius:50%;background:#eee;margin:0 auto 14px;display:flex;align-items:center;justify-content:center}
.feature h3{font-size:20px;font-weight:700;margin-bottom:8px}
.feature .lead{font-size:13px;color:#555;margin-bottom:6px}
.feature p{font-size:12px;line-height:20px;color:#666;text-align:left}
.feature .more{font-size:12px;color:var(--green-text);margin-top:10px}
.vdiv{top:630px;width:1px;height:200px;background:var(--line)}
.sidetab{left:1143px;top:614px;width:57px;height:144px;background:var(--green);border-radius:6px 0 0 6px}
.sidetab i{display:block;width:30px;height:30px;margin:14px auto 4px;border-radius:50%;background:#fff;opacity:.9}
.sidetab span{display:block;font-size:10px;color:#fff;text-align:center}
/* rate slider */
.rates{left:139px;top:884px;width:918px;height:46px;text-align:center;font-size:22px;line-height:46px}
.rates b{font-weight:700}
.rates .g{color:var(--blue)}
.arrow{top:896px}
/* table */
.table-box{left:139px;top:963px;width:918px;height:378px;border:1px solid #ddd;box-shadow:0 2px 6px rgba(0,0,0,.08)}
table{width:100%;border-collapse:collapse;font-size:13px}
thead th{height:51px;background:#f0f0f0;text-align:left;font-size:17px;font-weight:500;padding-left:18px}
tbody td{height:54px;border-top:1px solid #eee;padding-left:18px;color:#555}
tbody tr:nth-child(3) td{background:#f7f7f7}
.tag{display:inline-block;width:16px;height:16px;border-radius:50%;background:var(--green);color:#fff;font-size:10px;text-align:center;line-height:16px;margin-right:4px}
.tag.b{background:var(--blue)}
.bar{display:inline-block;vertical-align:middle;width:96px;height:10px;background:#ddd;border-radius:5px;overflow:hidden;margin-right:10px}
.bar i{display:block;height:100%;background:var(--green)}
.act{display:inline-block;width:64px;height:22px;line-height:22px;text-align:center;border-radius:11px;color:#fff;font-size:11px;background:var(--blue)}
.act.done{background:#b5b5b5}
/* stats */
.stats{left:139px;top:1372px;width:918px;height:72px}
.stat{position:absolute;top:0}
.stat b{font-size:22px;font-weight:700}
.stat small{display:block;font-size:11px;color:#888;margin-top:4px}
.stats-btn{left:932px;top:1394px;width:115px;height:38px;line-height:38px;font-size:16px}
/* products */
.section-title{font-size:22px;font-weight:700}
.cards{left:139px;top:1567px;width:918px;height:190px;display:flex}
.card{flex:1;padding:26px 24px;color:#fff}
.card .t{font-size:14px}
.card .v{font-size:28px;font-weight:700;margin:8px 0 4px}
.card .d{font-size:13px}
.card .btn{width:96px;height:34px;line-height:34px;font-size:15px;margin-top:16px}
/* partners */
.banks{left:280px;top:1864px;width:744px;display:grid;grid-template-columns:repeat(6,1fr);gap:18px 20px}
.bank{height:28px;display:flex;align-items:center;gap:8px}
.bank i{width:20px;height:20px;border-radius:50%;background:#d33}
.bank span{flex:1;height:12px;background:#c7c7c7;border-radius:2px}
.band{left:0;top:2011px;width:1200px;height:109px;background:var(--band)}
.plogo{top:2048px;height:30px;background:#cfcfcf;border-radius:3px}
/* footer */
.footer{left:0;top:2120px;width:1200px;height:337px;background:var(--footer)}
.contact{left:154px;top:2114px;width:903px;height:57px;background:var(--blue);border-radius:4px}
.soc{top:2124px;width:36px;height:36px;border-radius:4px;background:#3d4047}
.contact-btn{left:390px;top:2129px;width:220px;height:28px;line-height:28px;font-size:13px;border-radius:14px}
.phone{left:640px;top:2120px;color:#fff;text-align:center}
.phone small{display:block;font-size:10px}
.phone b{font-size:24px;font-weight:700;letter-spacing:1px}
.contact-links{left:875px;top:2126px;font-size:10px;line-height:16px;color:#fff}
.flinks{left:0;top:2205px;width:1200px;text-align:center;font-size:12px;line-height:26px;color:#ddd}
.flinks span{margin:0 12px}
.cert{top:2324px;width:90px;height:40px;background:#e8e8e8;border-radius:3px}
.copy{left:0;top:2420px;width:1200px;text-align:center;font-size:11px;color:#888}
</style>
</head>
<body>

<div class="topbar">
  <div class="field" style="left:356px">用户名 / 手机号</div>
  <div class="field" style="left:565px">请输入登录密码</div>
  <div class="login">立即登录</div>
  <div class="hint">新用户免费注册</div>
  <div class="lang"><i></i><b></b></div>
</div>

<div class="abs header"></div>
<div class="abs brand"><span class="dot"></span><span class="name">Kelumo</span></div>
<nav class="nav">
  <a style="left:496px">我要投资理财</a>
  <a style="left:707px">我要申请借款</a>
  <a style="left:946px">安全保障中心</a>
</nav>

<div class="abs hero" role="img" aria-label="商务人士团队合影，前景为手持文件的女性职员"></div>
<div class="abs hero-title">把致和多美傳致<br>合美 學舞統來舞求</div>
<div class="abs hero-text">安全透明的借贷平台 专业风控 本息保障<br>灵活投资期限 收益稳定 资金托管<br>低门槛 高收益 轻松理财</div>

<div class="abs strip"></div>
<div class="abs strip-slogan">助　力形形如思文<br>致文　力助台　為華文</div>
<div class="abs strip-mid">用傳己，自華致形規　自　料！</div>
<div class="abs strip-date">2014-07-17</div>
<svg class="abs" style="left:836px;top:500px" width="90" height="30" viewBox="0 0 90 30"><path d="M2 22 Q40 30 82 12" stroke="#333" stroke-width="2" fill="none"/><path d="M74 8 L84 12 L76 19" stroke="#333" stroke-width="2" fill="none"/></svg>
<div class="abs btn strip-btn">立即注册 ▸</div>

<div class="abs vdiv" style="left:422px"></div>
<div class="abs vdiv" style="left:770px"></div>
<div class="abs feature" style="left:281px">
  <div class="icon"><svg width="28" height="24"><rect x="2" y="14" width="5" height="10" fill="#f6a23d"/><rect x="10" y="8" width="5" height="16" fill="#4cb62a"/><rect x="18" y="2" width="5" height="22" fill="#2aa6e0"/></svg></div>
  <h3>收益</h3>
  <div class="lead">年化收益率最高可达15%</div>
  <p>一元起投，收益远高于银行存款，资金灵活，期限自由选择，每月按时回款。</p>
  <div class="more">了解更多　立即投资</div>
</div>
<div class="abs feature" style="left:594px">
  <div class="icon"><svg width="22" height="26"><rect x="2" y="10" width="18" height="14" rx="2" fill="#aaa"/><path d="M6 10 V6 a5 5 0 0 1 10 0 V10" stroke="#aaa" stroke-width="2.5" fill="none"/></svg></div>
  <h3>安全</h3>
  <div class="lead">本息保障　资金托管</div>
  <p>风险准备金全额垫付，第三方资金托管，借款人经过严格审核，保障出借人权益。</p>
  <div class="more">了解更多　立即投资</div>
</div>
<div class="abs feature" style="left:944px">
  <div class="icon"><svg width="26" height="26"><circle cx="13" cy="13" r="10" stroke="#aaa" stroke-width="2.5" fill="none"/><path d="M13 7 V13 L17 16" stroke="#aaa" stroke-width="2.5" fill="none"/></svg></div>
  <h3>便捷</h3>
  <div class="lead">快速审核　已放款</div>
  <p>在线申请，三步完成借款，最快当天放款，流程简单透明，随时查看进度。</p>
  <div class="more">了解更多　立即借款</div>
</div>
<div class="abs sidetab"><i></i><span>在线客服</span><i></i><span>意见反馈</span></div>

<svg class="abs arrow" style="left:139px" width="14" height="22"><path d="M12 2 L3 11 L12 20" stroke="#bbb" stroke-width="2.5" fill="none"/></svg>
<svg class="abs arrow" style="left:1043px" width="14" height="22"><path d="M2 2 L11 11 L2 20" stroke="#bbb" stroke-width="2.5" fill="none"/></svg>
<div class="abs rates"><span class="g">投资额</span>　<b>50000元 年利率15.0%</b>　　<span class="g">借款额</span>　<b>130元 年利率15.0%</b></div>

<div class="abs table-box">
<table>
  <thead><tr><th style="width:290px">借款标题</th><th style="width:100px">信用</th><th>年利率</th><th>金额</th><th>期限</th><th style="width:200px">进度</th><th></th></tr></thead>
  <tbody>
    <tr><td>装修资金周转借款 短期经营借款</td><td><span class="tag">A</span><span class="tag">认</span></td><td>15.0%</td><td>50,000 元</td><td>12 个月</td><td><span class="bar"><i style="width:7%"></i></span>6.69%</td><td><span class="act">我要投</span></td></tr>
    <tr><td>个体店铺扩大经营 短期资金周转</td><td><span class="tag">A</span><span class="tag">认</span><span class="tag b">抵</span></td><td>15.0%</td><td>8197.0 元</td><td>6 个月</td><td><span class="bar"><i style="width:9%"></i></span>9.23%</td><td><span class="act">我要投</span></td></tr>
    <tr><td>购车消费分期借款 按月还款</td><td><span class="tag">B</span><span class="tag">认</span><span class="tag b">抵</span></td><td>14.52%</td><td>12,782.0 元</td><td>9 个月</td><td><span class="bar"><i style="width:61%"></i></span>61.25%</td><td><span class="act">我要投</span></td></tr>
    <tr><td>小微企业经营借款 设备采购</td><td><span class="tag">A</span><span class="tag">认</span></td><td>15.0%</td><td>50,000 元</td><td>12 个月</td><td><span class="bar"><i style="width:100%"></i></span>100.0%</td><td><span class="act done">还款中</span></td></tr>
    <tr><td>婚庆消费借款 家庭装修</td><td><span class="tag">A</span><span class="tag">认</span></td><td>15.0%</td><td>40,000 元</td><td>12 个月</td><td><span class="bar"><i style="width:100%"></i></span>100.0%</td><td><span class="act done">还款中</span></td></tr>
    <tr><td>教育进修 个人借款</td><td><span class="tag">A</span><span class="tag">认</span></td><td>15.0%</td><td>50,000 元</td><td>12 个月</td><td><span class="bar"><i style="width:100%"></i></span>100.0%</td><td><span class="act done">还款中</span></td></tr>
  </tbody>
</table>
</div>

<div class="abs stats">
  <div class="stat" style="left:0"><b>¥ 160407</b><small>平台累计成交金额　　投资总额</small></div>
  <div class="stat" style="left:226px"><b>14.69%</b><small>平均年化收益率　　出借收益</small></div>
  <div class="stat" style="left:471px"><b>12.24 億美統合霖</b><small>累计为用户赚取收益　　数据实时更新</small></div>
</div>
<svg class="abs" style="left:850px;top:1388px" width="80" height="30" viewBox="0 0 80 30"><path d="M2 22 Q36 30 72 12" stroke="#333" stroke-width="2" fill="none"/><path d="M64 8 L74 12 L66 19" stroke="#333" stroke-width="2" fill="none"/></svg>
<div class="abs btn stats-btn">自由投 ▸</div>

<div class="abs section-title" style="left:139px;top:1510px">校如形康</div>
<div class="abs cards">
  <div class="card" style="background:var(--orange)"><div class="t">短期理财计划</div><div class="v">10.0%</div><div class="d">期限灵活，收益稳定可靠</div><div class="btn">立即投</div></div>
  <div class="card" style="background:var(--yellow)"><div class="t">季度理财计划</div><div class="v">11.0%</div><div class="d">期限灵活，收益稳定可靠</div><div class="btn">立即投</div></div>
  <div class="card" style="background:var(--pink)"><div class="t">半年理财计划</div><div class="v">12.0%</div><div class="d">期限灵活，收益稳定可靠</div><div class="btn">立即投</div></div>
  <div class="card" style="background:var(--purple)"><div class="t">年度理财计划</div><div class="v">13.0%</div><div class="d">期限灵活，收益稳定可靠</div><div class="btn">立即投</div></div>
</div>

<div class="abs section-title" style="left:0;width:1200px;top:1804px;text-align:center">交機致學舞求來　名多多美解統合</div>
<svg class="abs" style="left:139px;top:1888px" width="16" height="26"><path d="M14 2 L3 13 L14 24" stroke="#bbb" stroke-width="2.5" fill="none"/></svg>
<svg class="abs" style="left:1041px;top:1888px" width="16" height="26"><path d="M2 2 L13 13 L2 24" stroke="#bbb" stroke-width="2.5" fill="none"/></svg>
<div class="abs banks">
  <div class="bank"><i></i><span></span></div><div class="bank"><i></i><span></span></div><div class="bank"><i style="background:#1a5fa8"></i><span></span></div><div class="bank"><i></i><span></span></div><div class="bank"><i></i><span></span></div><div class="bank"><i></i><span></span></div>
  <div class="bank"><i></i><span></span></div><div class="bank"><i style="background:#1a5fa8"></i><span></span></div><div class="bank"><i style="background:#1a5fa8"></i><span></span></div><div class="bank"><i style="background:#2a8a3a"></i><span></span></div><div class="bank"><i style="background:#1a5fa8"></i><span></span></div><div class="bank"><i></i><span></span></div>
</div>

<div class="abs band"></div>
<div class="abs plogo" style="left:139px;width:112px"></div>
<div class="abs plogo" style="left:305px;width:150px"></div>
<div class="abs plogo" style="left:485px;width:175px"></div>
<div class="abs plogo" style="left:692px;width:30px"></div>
<div class="abs plogo" style="left:787px;width:75px"></div>
<div class="abs plogo" style="left:905px;width:150px"></div>

<div class="abs footer"></div>
<div class="abs contact"></div>
<div class="abs soc" style="left:168px"></div>
<div class="abs soc" style="left:220px"></div>
<div class="abs soc" style="left:272px"></div>
<div class="abs soc" style="left:324px"></div>
<div class="abs btn contact-btn">在线客服咨询　常见问题解答</div>
<div class="abs phone"><small>客服热线 工作日 9:00-18:00</small><b>400 - 700 - 2468</b></div>
<div class="abs contact-links">关注我们 微博 微信<br>帮助中心 新手指引</div>
<div class="abs flinks">
  <div><span>关于我们</span><span>公司简介</span><span>管理团队</span><span>新闻动态</span><span>招贤纳士</span><span>联系我们</span><span>合作伙伴</span></div>
  <div><span>安全保障</span><span>风险准备金</span><span>资金托管</span><span>法律政策</span><span>隐私条款</span></div>
  <div><span>新手指引</span><span>常见问题</span><span>借款流程</span><span>投资流程</span><span>资费说明</span></div>
</div>
<div class="abs cert" style="left:280px"></div>
<div class="abs cert" style="left:400px"></div>
<div class="abs cert" style="left:520px"></div>
<div class="abs cert" style="left:690px"></div>
<div class="abs cert" style="left:810px"></div>
<div class="abs copy">© 2014 Kelumo.cn 版权所有　沪ICP备00000000号</div>

</body>
</html>
```